Venture 482 - Lumora Book Cover

I am looking for a Lumora book cover for my book about "Venture 482".
The Book is Titled:
Venture 482 Ascended
Shaping Outcomes: Paths To Unlocking Cosmic Truths
Author is Dorian Pell
Here is a book description that may help you understand more about it:
Inspired by the genius of Edwin Marlowe, this comprehensive guide delves into the ancient wisdom and cutting-edge science behind the 482 method, a powerful tool for manifesting your desires. Whether you're seeking personal growth, financial success, or spiritual enlightenment, this book provides advanced techniques and methods to transform your dreams into reality.
Any questions please ask.
Thanks
Owen

```html
<!DOCTYPE html>
<html lang="en">
<head>
<meta charset="utf-8">
<title>Venture 482 Ascended — Lumora Cover</title>
<link rel="stylesheet" href="https://fonts.googleapis.com/css2?family=Cinzel:wght@400;500&family=Tinos:wght@400;700&display=swap">
<style>
  :root {
    --page-bg: #e7e7e6;
    --cover-deep: #05090b;
    --cover-teal: #0f3a40;
    --cover-mid: #0a2329;
    --title-cream: #f4eadc;
    --author-blush: #f1ddd3;
    --band-cream: #fbf9e1;
    --band-ink: #2a2a66;
    --emblem-light: rgba(235, 240, 238, 0.28);
    --emblem-edge: rgba(235, 240, 238, 0.05);
    --white: #ffffff;
  }
  * { margin: 0; padding: 0; box-sizing: border-box; }
  html, body {
    width: 1200px;
    height: 1131px;
    overflow: hidden;
    background: var(--page-bg);
  }
  .cover {
    position: absolute;
    left: 246px;
    top: 30px;
    width: 708px;
    height: 1071px;
    overflow: hidden;
    background:
      radial-gradient(ellipse 90% 55% at 55% 22%, var(--cover-teal) 0%, transparent 75%),
      linear-gradient(180deg, var(--cover-mid) 0%, #0c2c31 40%, #071519 72%, var(--cover-deep) 100%);
  }
  .cover-title {
    position: absolute;
    top: 140px;
    left: 0;
    width: 100%;
    text-align: center;
    font-family: "Cinzel", "Times New Roman", serif;
    font-weight: 400;
    font-size: 88px;
    letter-spacing: 1px;
    color: var(--title-cream);
    line-height: 1;
  }
  .emblem {
    position: absolute;
    left: 90px;
    top: 223px;
    width: 540px;
    height: 507px;
  }
  .emblem-number {
    position: absolute;
    left: 90px;
    top: 430px;
    width: 540px;
    text-align: center;
    font-family: "Tinos", "Times New Roman", serif;
    font-size: 76px;
    font-weight: 400;
    color: var(--white);
    line-height: 1;
  }
  .edition-band {
    position: absolute;
    left: 171px;
    top: 730px;
    width: 380px;
    height: 47px;
    background: var(--band-cream);
    display: flex;
    align-items: center;
    justify-content: center;
    font-family: "Cinzel", "Times New Roman", serif;
    font-size: 27px;
    letter-spacing: 21px;
    padding-left: 21px;
    color: var(--band-ink);
  }
  .subtitle {
    position: absolute;
    top: 798px;
    left: 0;
    width: 100%;
    text-align: center;
    font-family: "Tinos", "Times New Roman", serif;
    color: var(--white);
  }
  .subtitle-lead {
    font-weight: 700;
    font-size: 24px;
    line-height: 30px;
  }
  .subtitle-rest {
    font-weight: 400;
    font-size: 22px;
    line-height: 33px;
  }
  .author {
    position: absolute;
    top: 982px;
    left: 0;
    width: 100%;
    text-align: center;
    font-family: "Cinzel", "Times New Roman", serif;
    font-size: 54px;
    letter-spacing: 19px;
    padding-left: 19px;
    color: var(--author-blush);
    line-height: 1;
  }
</style>
</head>
<body>
  <main class="cover">
    <h1 class="cover-title">VENTURE</h1>

    <svg class="emblem" viewBox="0 0 540 507" role="img" aria-label="Sacred geometry emblem: concentric circles, star rays and orbiting glyphs around the central number">
      <defs>
        <radialGradient id="emblemGlow" cx="50%" cy="50%" r="50%">
          <stop offset="0%" stop-color="var(--emblem-light)"/>
          <stop offset="100%" stop-color="var(--emblem-edge)"/>
        </radialGradient>
      </defs>
      <ellipse cx="270" cy="253" rx="265" ry="250" fill="url(#emblemGlow)"/>
    </svg>
    <div class="emblem-number">482</div>

    <div class="edition-band">ASCENDED</div>

    <div class="subtitle">
      <p class="subtitle-lead">SHAPING OUTCOMES:</p>
      <p class="subtitle-rest">Paths to unlocking<br>cosmic truths</p>
    </div>

    <p class="author">DORIAN PELL</p>
  </main>
</body>
</html>
```